Business card design Needed for new logo / Construction business, home extensions and new builds

We need a business card design using our new logo files which i will attach to this project :)

We are a small construction business specialising in home extensions, new builds and property development. We are very ambitious and would appreciate professional and elegant designs for our new business card.

Very serious about using the services on MakerQuarry and recently acquired our new logo from here :)

Please get involved, i will feedback when i can as i am very busy but can respond daily, thanks

Target Market(s)

People that want to build onto their houses, new building developments or adding too their existing property

Industry/Entity Type

Construction

Contact Information for Business Card

Renwick Tolliver Construction, Lionel Ashby (Managing Director), Tel 07822254961, email - info@renwick-tolliver, www.renwick-tolliver.co.uk

Colors

Designer to choose colors to be used in the design.

Requirements
Must have
• I like a deep grey on the back please. A lot of you have provided black from and back, try mixing things up a little. The black looks cool 😎 Thanks

```html
<!DOCTYPE html>
<html lang="en">
<head>
<meta charset="utf-8">
<title>Renwick Tolliver Construction – Business Card</title>
<link rel="stylesheet" href="https://fonts.googleapis.com/css2?family=Cinzel:wght@500;600&family=Poppins:wght@400;500&display=swap">
<style>
  :root{
    --backdrop:#2c2d2f;
    --card-front:#1a1b1d;
    --card-back-dark:#121314;
    --card-back-light:#2e2f31;
    --gold:#d9a22b;
    --gold-deep:#b8821a;
    --silver:#d6d8da;
    --silver-dim:#9a9da1;
  }
  *{margin:0;padding:0;box-sizing:border-box}
  html,body{width:1200px;height:1108px;overflow:hidden}
  body{background:var(--backdrop);position:relative;font-family:"Poppins",sans-serif}

  .card{position:absolute;top:214px;width:430px;height:680px;border-radius:24px;box-shadow:0 18px 40px rgba(0,0,0,.45)}
  .card-front{left:150px;background:var(--card-front);text-align:center}
  .card-back{left:620px;overflow:hidden}

  .brand-square{position:absolute;top:140px;left:50%;width:56px;height:56px;margin-left:-28px;background:var(--gold);border-radius:4px}
  .company-name{position:absolute;top:228px;left:0;right:0;font-family:"Cinzel",serif;font-weight:600;color:var(--silver);font-size:30px;line-height:1.25;letter-spacing:1px}
  .company-rule{position:absolute;top:320px;left:50%;width:240px;margin-left:-120px;height:2px;background:linear-gradient(90deg,transparent,var(--gold) 20%,var(--gold) 80%,transparent)}

  .person-name{position:absolute;top:356px;left:0;right:0;font-family:"Cinzel",serif;font-weight:500;color:var(--silver);font-size:21px;letter-spacing:1px}
  .person-role{position:absolute;top:386px;left:0;right:0;color:var(--gold);font-size:17px}

  .icon-row{position:absolute;top:430px;left:50px;right:50px;height:34px;display:flex;align-items:center;justify-content:center;gap:8px}
  .icon-row::before,.icon-row::after{content:"";flex:1;height:1px;background:var(--gold-deep)}
  .icon-tile{width:32px;height:32px;border-radius:5px;background:linear-gradient(145deg,#f1f2f3,#8e9196);display:flex;align-items:center;justify-content:center}
  .icon-tile svg{width:20px;height:20px}

  .contact-list{position:absolute;top:480px;left:0;right:0;list-style:none;color:var(--gold);font-size:19px;line-height:30px}
  .contact-rule{position:absolute;top:586px;left:70px;right:70px;height:1px;background:var(--gold-deep)}
  .address{position:absolute;top:600px;left:0;right:0;color:var(--gold);font-size:18px;line-height:26px;font-style:normal}

  .back-pattern{position:absolute;inset:0;background:linear-gradient(135deg,var(--card-back-dark) 0%,#1c1d1f 50%,var(--card-back-light) 100%)}
  .back-mark{position:absolute;right:40px;bottom:90px;display:flex;align-items:center;gap:8px;color:var(--gold);font-size:15px;font-weight:500}
  .back-mark-square{width:16px;height:16px;background:var(--gold);border-radius:2px}
</style>
</head>
<body>
  <section class="card card-front" aria-label="Business card front">
    <div class="brand-square"></div>
    <h1 class="company-name">RENWICK TOLLIVER<br>CONSTRUCTION</h1>
    <div class="company-rule"></div>

    <p class="person-name">JULIAN MARSH</p>
    <p class="person-role">Managing Director</p>

    <div class="icon-row">
      <span class="icon-tile" aria-label="Phone">
        <svg viewBox="0 0 24 24"><path d="M6.6 10.8a15 15 0 0 0 6.6 6.6l2.2-2.2c.3-.3.7-.4 1-.2 1.1.4 2.3.6 3.6.6.6 0 1 .4 1 1V20c0 .6-.4 1-1 1A17 17 0 0 1 3 4c0-.6.4-1 1-1h3.5c.6 0 1 .4 1 1 0 1.2.2 2.5.6 3.6.1.3 0 .7-.2 1z" fill="#222"/></svg>
      </span>
      <span class="icon-tile" aria-label="Email">
        <svg viewBox="0 0 24 24"><rect x="3" y="6" width="18" height="12" rx="1" fill="none" stroke="#222" stroke-width="2"/><path d="M3 7l9 6 9-6" fill="none" stroke="#222" stroke-width="2"/></svg>
      </span>
      <span class="icon-tile" aria-label="Website">
        <svg viewBox="0 0 24 24"><circle cx="12" cy="12" r="8.5" fill="none" stroke="#222" stroke-width="2"/><path d="M3.5 12h17M12 3.5c2.5 2.5 2.5 14.5 0 17M12 3.5c-2.5 2.5-2.5 14.5 0 17" fill="none" stroke="#222" stroke-width="1.6"/></svg>
      </span>
    </div>

    <ul class="contact-list">
      <li>078 2225 4961</li>
      <li>info@renwick-tolliver.co.uk</li>
      <li>www.renwick-tolliver.co.uk</li>
    </ul>
    <div class="contact-rule"></div>
    <address class="address">421, Address line goes here<br>45452, Country Name</address>
  </section>

  <section class="card card-back" aria-label="Business card back">
    <div class="back-pattern" role="img" aria-label="Repeating tone-on-tone monogram pattern in glossy black"></div>
    <div class="back-mark"><span class="back-mark-square"></span>Renwick Tolliver</div>
  </section>
</body>
</html>
```